Verodex business card

Business card for sustainable investment company called "Verodex". Verodex is an exchange platform selling carbon credits between buyers and sellers. Carbon Credits are an environmental commodity for reducing global carbon emissions.

the card should obviously have our logo and the theme should be sustainability/environment mixed with a trading platform.

Contact Information for Business Card

Logo, Name, Title, Phone, Email

Colors
0054AA
0677BA
7BADD7
CADEEF
E8F1F8
0094D4
00A9DD
6FCCEA
C7EBF8
E9F6FB
00AB8E
00BBA5
67D7C9
C6EFE9
E9F9F6
59FF00
82FF00
B8FF75
E3FFCB
F4FFEA

```html
<!DOCTYPE html>
<html lang="en">
<head>
<meta charset="utf-8">
<title>Verodex Business Card</title>
<link rel="stylesheet" href="https://fonts.googleapis.com/css2?family=Poppins:wght@400;500;600&display=swap">
<style>
  :root {
    --backdrop: #6a6a6a;
    --card-light: #ffffff;
    --card-dark: #22344f;
    --navy: #22344f;
    --ink: #1c1c1c;
    --accent: #2a86e6;
    --divider: #b9b9b9;
  }
  * { margin: 0; padding: 0; box-sizing: border-box; }
  html, body {
    width: 1093px;
    height: 1200px;
    overflow: hidden;
    background: var(--backdrop);
    font-family: "Poppins", sans-serif;
  }
  .card {
    position: absolute;
    left: 265px;
    width: 578px;
    height: 356px;
    border-radius: 24px;
    box-shadow: 3px 4px 4px rgba(0,0,0,0.55);
  }
  .card--front { top: 226px; background: var(--card-light); }
  .card--back { top: 621px; background: var(--card-dark); }

  .brand {
    position: absolute;
    display: flex;
    align-items: center;
  }
  .brand__dot {
    border-radius: 50%;
    background: var(--accent);
  }
  .brand__name {
    font-weight: 600;
    letter-spacing: 0.5px;
    line-height: 1;
  }
  .card--front .brand { left: 42px; top: 158px; gap: 14px; }
  .card--front .brand__dot { width: 40px; height: 40px; }
  .card--front .brand__name { font-size: 32px; color: var(--navy); }

  .card--back .brand { left: 128px; top: 150px; gap: 20px; }
  .card--back .brand__dot { width: 58px; height: 58px; }
  .card--back .brand__name { font-size: 45px; color: #ffffff; }

  .divider {
    position: absolute;
    left: 288px;
    top: 74px;
    width: 1px;
    height: 210px;
    background: linear-gradient(to bottom, transparent, var(--divider) 15%, var(--divider) 85%, transparent);
  }
  .person {
    position: absolute;
    left: 311px;
    top: 106px;
  }
  .person__name {
    font-size: 23px;
    font-weight: 600;
    color: var(--navy);
    line-height: 1.05;
    letter-spacing: 0.3px;
  }
  .person__title {
    font-size: 17px;
    font-weight: 400;
    color: #333;
    line-height: 1.1;
  }
  .contacts {
    position: absolute;
    left: 311px;
    top: 181px;
    list-style: none;
  }
  .contacts__item {
    display: flex;
    align-items: center;
    gap: 7px;
    height: 21px;
    font-size: 17.5px;
    color: var(--ink);
    white-space: nowrap;
  }
  .contacts__icon { width: 15px; height: 15px; fill: var(--navy); flex: none; }
  .contacts__domain { color: var(--navy); }
</style>
</head>
<body>
  <section class="card card--front">
    <div class="brand">
      <span class="brand__dot"></span>
      <span class="brand__name">VERODEX</span>
    </div>
    <div class="divider"></div>
    <div class="person">
      <p class="person__name">MARCUS HALE</p>
      <p class="person__title">Managing Director</p>
    </div>
    <ul class="contacts">
      <li class="contacts__item">
        <svg class="contacts__icon" viewBox="0 0 24 24" aria-hidden="true"><path d="M6.6 10.8a15.1 15.1 0 0 0 6.6 6.6l2.2-2.2a1 1 0 0 1 1-.25 11.4 11.4 0 0 0 3.6.6 1 1 0 0 1 1 1V20a1 1 0 0 1-1 1A17 17 0 0 1 3 4a1 1 0 0 1 1-1h3.5a1 1 0 0 1 1 1c0 1.25.2 2.45.6 3.6a1 1 0 0 1-.25 1z"/></svg>
        <span>041-870 235 614</span>
      </li>
      <li class="contacts__item">
        <svg class="contacts__icon" viewBox="0 0 24 24" aria-hidden="true"><path d="M2 5h20v14H2z M2 5l10 8 10-8" fill="none" stroke="#22344f" stroke-width="2.2"/><path d="M2 5h20l-10 8z"/></svg>
        <span>hello@verodex.com</span>
      </li>
      <li class="contacts__item">
        <svg class="contacts__icon" viewBox="0 0 24 24" aria-hidden="true"><g fill="none" stroke="#22344f" stroke-width="1.8"><circle cx="12" cy="12" r="10"/><ellipse cx="12" cy="12" rx="4.5" ry="10"/><path d="M2 12h20M4 7h16M4 17h16"/></g></svg>
        <span>www.<span class="contacts__domain">verodextrade</span>.com</span>
      </li>
    </ul>
  </section>

  <section class="card card--back">
    <div class="brand">
      <span class="brand__dot"></span>
      <span class="brand__name">VERODEX</span>
    </div>
  </section>
</body>
</html>
```